Business card for my new company (Accounting firm)

I need a business card for my new business Brightwell Advisory and Ledger SA. Our services are accounting, tax, audit and financial management. Our customers are small companies, start-ups and new companies. The final design has to show financial security, trust and growth. Please find our logo attached to the business card. Text for the business card: Brightwell Advisory and Ledger SA Tomas Varenholt Director and Founder Certified Accountant Tel. 022 418 57 34 tv@clairevalconseil.ch www.clairevalconseil.ch Rue des Vergières 27 1201 Geneva
Target Market(s)
Our customers are small companies, start-ups and new companies.
Industry/Entity Type
Finance And Accounting
Contact Information for Business Card
Claireval Conseil et Comptes SA
Tomas Varenholt
Directeur et Fondateur
Expert-comptable diplômé
Tél. 022 418 57 34
tv@clairevalconseil.ch
www.clairevalconseil.ch
Rue des Vergières 27
1201 Genève

```html
<!DOCTYPE html>
<html lang="fr">
<head>
<meta charset="utf-8">
<title>Claireval Conseil et Comptes SA – Carte de visite</title>
<link rel="stylesheet" href="https://fonts.googleapis.com/css2?family=Roboto:wght@400;500;700&display=swap">
<style>
  :root {
    --page-bg: #d8d3ce;
    --card-top: #f3f4f5;
    --card-bottom: #e4e7e9;
    --card-edge: #c9cdd0;
    --brand-blue: #1d5f8f;
    --accent-blue: #2a8cc4;
    --text-dark: #3a3d40;
    --icon-dark: #2f4150;
  }
  * { margin: 0; padding: 0; box-sizing: border-box; }
  html, body {
    width: 1200px;
    height: 1054px;
    overflow: hidden;
    background: var(--page-bg);
    font-family: "Roboto", Arial, sans-serif;
  }
  .stage {
    width: 1200px;
    height: 1054px;
    display: flex;
    align-items: center;
    justify-content: center;
  }
  .business-card {
    position: relative;
    width: 1000px;
    height: 600px;
    background: linear-gradient(160deg, var(--card-top), var(--card-bottom));
    border: 1px solid var(--card-edge);
    box-shadow: 0 18px 40px rgba(0, 0, 0, 0.12);
  }
  .holder {
    position: absolute;
    left: 41px;
    top: 80px;
  }
  .holder-name {
    font-size: 34px;
    font-weight: 700;
    color: var(--brand-blue);
    letter-spacing: 0.2px;
    margin-bottom: 14px;
  }
  .holder-role {
    font-size: 22px;
    font-weight: 400;
    color: var(--text-dark);
    line-height: 30px;
  }
  .address {
    position: absolute;
    left: 41px;
    top: 352px;
    font-size: 23px;
    line-height: 38px;
    color: var(--text-dark);
  }
  .contact-list {
    position: absolute;
    left: 41px;
    top: 448px;
    list-style: none;
  }
  .contact-item {
    display: flex;
    align-items: center;
    height: 38px;
    font-size: 23px;
    color: var(--text-dark);
  }
  .contact-icon {
    width: 20px;
    height: 20px;
    margin-right: 26px;
    fill: var(--icon-dark);
  }
  .brand {
    position: absolute;
    right: 40px;
    bottom: 40px;
    display: flex;
    flex-direction: column;
    align-items: flex-end;
  }
  .brand-square {
    width: 56px;
    height: 56px;
    background: var(--accent-blue);
    margin-bottom: 22px;
  }
  .brand-name {
    font-size: 30px;
    font-weight: 500;
    color: var(--text-dark);
    line-height: 38px;
    text-align: right;
    letter-spacing: 1.5px;
  }
</style>
</head>
<body>
<main class="stage">
  <article class="business-card">
    <header class="holder">
      <h1 class="holder-name">Tomas Varenholt</h1>
      <p class="holder-role">Directeur et Fondateur</p>
      <p class="holder-role">Expert-comptable diplômé</p>
    </header>

    <address class="address" style="font-style: normal;">
      Rue des Vergières 27<br>
      1201 Genève
    </address>

    <ul class="contact-list">
      <li class="contact-item">
        <svg class="contact-icon" viewBox="0 0 20 20" aria-hidden="true">
          <path d="M2 7c0-2 3-4 8-4s8 2 8 4v1.5h-4V6.8c-1-.5-2.5-.8-4-.8s-3 .3-4 .8v1.7H2z"/>
          <path d="M5 10l2-2.5h6L15 10v7H5z"/>
        </svg>
        022 418 57 34
      </li>
      <li class="contact-item">
        <svg class="contact-icon" viewBox="0 0 20 20" aria-hidden="true">
          <path d="M1 4h18v12H1z M2.5 5.5L10 11l7.5-5.5" fill="none" stroke="#2f4150" stroke-width="1.8"/>
        </svg>
        tv@clairevalconseil.ch
      </li>
      <li class="contact-item">
        <svg class="contact-icon" viewBox="0 0 20 20" aria-hidden="true">
          <g fill="none" stroke="#2f4150" stroke-width="1.6">
            <circle cx="10" cy="10" r="8"/>
            <ellipse cx="10" cy="10" rx="3.5" ry="8"/>
            <path d="M2 10h16"/>
          </g>
        </svg>
        www.clairevalconseil.ch
      </li>
    </ul>

    <div class="brand">
      <div class="brand-square" aria-hidden="true"></div>
      <p class="brand-name">CLAIREVAL<br>CONSEIL ET COMPTES</p>
    </div>
  </article>
</main>
</body>
</html>
```